Flat bootstrap design for existing site

I'm looking for a modern flat design based around an existing logo. This has to be a custom design (no external templates), and implemented into a bootstrap framework.

The logo is attached as 2 versions - choose whichever you want, that flows better with whatever design you choose.

Added screenshots of the existing site (currently using the default bootstrap layouts). Please make your designs around those pages in the screenshots (i.e. the homepage only has the postal code input and the header). The active page has 3 screenshots, because I wanted to illustrate the other states that would be visible (in the table rows).

This is a moving/junk removal website, just for some context.

Here's some example websites (flat designs) that I like, just to give you an idea of what I'm after.

https://www.plimvora.com/
https://dacklow.com/
https://trevanu.com/
https://quobrintal.com/en/

Coding

Coded - Design and coding required

Number of Pages Required

5+ page

Colors

Designer to choose colors to be used in the design.

Requirements
Must have
• It must be a modern/simple flat design, that is built around the existing logo (attached).
• It has to be implemented using bootstrap.

```html
<!DOCTYPE html>
<html lang="en">
<head>
<meta charset="utf-8">
<title>Tarnello — Junk Removal</title>
<link href="https://fonts.googleapis.com/css2?family=Lato:wght@400;700;900&family=Open+Sans:wght@400&display=swap" rel="stylesheet">
<style>
  :root {
    --brand-blue: #3ec3f1;
    --button-blue: #29b8ec;
    --button-edge: #1589b6;
    --ink-dark: #262626;
    --ink-nav: #555555;
    --ink-muted: #666666;
    --field-border: #cfcfcf;
    --field-bg: #f1f1f1;
    --rule: #cccccc;
    --bg-light: #f7f7f7;
    --bg-mid: #eeeeee;
  }
  * { box-sizing: border-box; margin: 0; padding: 0; }
  html, body { width: 1200px; height: 702px; overflow: hidden; }
  body {
    position: relative;
    font-family: "Lato", Arial, sans-serif;
    background: var(--bg-light);
  }
  .page-backdrop {
    position: absolute; inset: 0;
    background: linear-gradient(135deg, var(--bg-light) 0%, var(--bg-mid) 35%, var(--bg-light) 60%, var(--bg-mid) 100%);
  }
  .site-header {
    position: absolute; left: 97px; right: 98px; top: 13px; height: 80px;
    display: flex; align-items: center; justify-content: space-between;
  }
  .brand {
    display: flex; align-items: center; gap: 10px;
    font-weight: 900; font-size: 34px; letter-spacing: 1px;
    color: var(--brand-blue); text-decoration: none;
  }
  .brand-dot {
    width: 22px; height: 22px; border-radius: 50%;
    background: var(--brand-blue);
  }
  .main-nav { display: flex; gap: 38px; margin-top: -12px; }
  .main-nav a {
    font-size: 15.5px; color: var(--ink-nav); text-decoration: none;
    padding-bottom: 4px; border-bottom: 1px solid transparent;
  }
  .main-nav a.is-active { border-bottom-color: var(--brand-blue); }
  .hero {
    position: absolute; left: 0; right: 0; top: 240px;
    text-align: center;
  }
  .hero-title {
    font-weight: 900; font-size: 42px; color: var(--ink-dark);
    text-shadow: 0 3px 4px rgba(0,0,0,0.25);
    letter-spacing: 0.2px;
  }
  .booking-form {
    position: absolute; left: 399px; top: 369px;
    display: flex; gap: 18px;
  }
  .postal-input {
    width: 283px; height: 43px; padding: 0 13px;
    border: 2px solid var(--field-border); background: var(--field-bg);
    font-family: "Lato", Arial, sans-serif; font-size: 15.5px; color: var(--ink-dark);
  }
  .postal-input::placeholder { color: #a8a8a8; }
  .book-button {
    width: 100px; height: 44px;
    background: var(--button-blue); color: #fff;
    border: none; border-bottom: 3px solid var(--button-edge);
    font-family: "Lato", Arial, sans-serif; font-weight: 700; font-size: 18px;
  }
  .site-footer {
    position: absolute; left: 99px; right: 100px; top: 645px;
    border-top: 1px solid var(--rule);
    text-align: center; padding-top: 25px;
    font-family: "Open Sans", Arial, sans-serif; font-size: 12.5px; color: var(--ink-muted);
  }
</style>
</head>
<body>
  <div class="page-backdrop" role="img" aria-label="Soft light grey low-poly geometric background"></div>

  <header class="site-header">
    <a class="brand" href="#"><span class="brand-dot"></span>TARNELLO</a>
    <nav class="main-nav">
      <a href="#">BOOK</a>
      <a href="#">HOW IT WOWS</a>
      <a href="#" class="is-active">BECOME A DRIVER</a>
      <a href="#">SIGN IN</a>
    </nav>
  </header>

  <section class="hero">
    <h1 class="hero-title">NEED JUNK REMOVED? BOOK NOW.</h1>
  </section>

  <form class="booking-form">
    <input class="postal-input" type="text" placeholder="Postal Code">
    <button class="book-button" type="button">BOOK</button>
  </form>

  <footer class="site-footer">© Copyright 2017 Tarnello. All Rights Reserved</footer>
</body>
</html>
```